FunBrixo Business Card

We need a business card design for our company. We sell construction-themed amusement rides for kids.

Contact Information for Business Card

Contact info on business card should include:
Carl Dunning
Co-Founder & COO
(833) 571-FUNBRIX
Carl@funbrixo-demo.com
www.funbrixo-demo.com

```html
<!DOCTYPE html>
<html lang="en">
<head>
<meta charset="utf-8">
<title>FunBrixo Business Card</title>
<link href="https://fonts.googleapis.com/css2?family=Poppins:wght@400;500;700;800&display=swap" rel="stylesheet">
<style>
  :root {
    --backdrop: #e6e7e9;
    --card: #1b1b1d;
    --card-edge: #f08a2c;
    --brand-orange: #f07f2d;
    --brand-purple: #8a3aa6;
    --accent-magenta: #c834c9;
    --rule-purple: #7b2f96;
    --text-light: #e4e4e4;
  }
  * { margin: 0; padding: 0; box-sizing: border-box; }
  html, body {
    width: 1200px; height: 801px; overflow: hidden;
    background: var(--backdrop);
    font-family: "Poppins", sans-serif;
  }
  .stage {
    position: relative; width: 1200px; height: 801px;
  }
  .card {
    position: absolute;
    background: var(--card);
    border: 2px solid var(--card-edge);
    box-shadow: 0 18px 40px rgba(0,0,0,0.28);
    overflow: hidden;
  }

  /* Back side (portrait) */
  .card--back {
    left: 90px; top: 120px;
    width: 320px; height: 560px;
  }
  .card--back .brand {
    position: absolute; top: 44px; left: 0; right: 0;
    display: flex; align-items: center; justify-content: center; gap: 8px;
  }
  .brand__name {
    font-weight: 800; color: var(--brand-orange);
    letter-spacing: -0.5px;
  }
  .brand__dot {
    border-radius: 50%; background: var(--brand-purple);
    flex: none;
  }
  .card--back .brand__name { font-size: 30px; }
  .card--back .brand__dot { width: 20px; height: 20px; }
  .card--back .header-rule {
    position: absolute; top: 122px; left: 22px; right: 22px;
    height: 1.5px; background: var(--rule-purple);
  }
  .contact-block {
    position: absolute;
    left: 40px; bottom: 36px;
    width: 300px;
    transform-origin: left bottom;
    transform: rotate(-90deg) translateY(100%);
  }
  .contact-block__name {
    font-weight: 700; font-size: 19px; color: var(--accent-magenta);
    text-transform: uppercase; line-height: 1.1;
  }
  .contact-block__title {
    font-size: 13.5px; color: var(--accent-magenta); margin-top: 2px;
  }
  .contact-block__rule {
    height: 1.5px; width: 210px; background: var(--rule-purple);
    margin: 8px 0 7px;
  }
  .contact-list { list-style: none; }
  .contact-list li {
    display: flex; align-items: center; gap: 8px;
    font-size: 13px; color: var(--text-light); line-height: 1.5;
  }
  .contact-list svg { width: 11px; height: 11px; flex: none; fill: var(--accent-magenta); }

  /* Front side (landscape) */
  .card--front {
    left: 460px; top: 200px;
    width: 680px; height: 400px;
  }
  .card--front .brand {
    position: absolute; inset: 0;
    display: flex; align-items: center; justify-content: center; gap: 16px;
  }
  .card--front .brand__name { font-size: 76px; }
  .card--front .brand__dot { width: 44px; height: 44px; }
</style>
</head>
<body>
<main class="stage">

  <section class="card card--back" aria-label="Card back">
    <div class="brand">
      <span class="brand__name">FunBrixo</span>
      <span class="brand__dot"></span>
    </div>
    <div class="header-rule"></div>

    <div class="contact-block">
      <p class="contact-block__name">Carl Dunning</p>
      <p class="contact-block__title">Co-Founder &amp; COO</p>
      <div class="contact-block__rule"></div>
      <ul class="contact-list">
        <li>
          <svg viewBox="0 0 24 24" aria-hidden="true"><path d="M6.6 10.8a15.1 15.1 0 0 0 6.6 6.6l2.2-2.2a1 1 0 0 1 1-.25 11.4 11.4 0 0 0 3.6.57 1 1 0 0 1 1 1V20a1 1 0 0 1-1 1A17 17 0 0 1 3 4a1 1 0 0 1 1-1h3.5a1 1 0 0 1 1 1c0 1.25.2 2.45.57 3.57a1 1 0 0 1-.25 1z"/></svg>
          <span>(833) 571-FUNBRIX</span>
        </li>
        <li>
          <svg viewBox="0 0 24 24" aria-hidden="true"><path d="M2 5h20v14H2z M4 7v.5l8 5 8-5V7l-8 5z" fill-rule="evenodd"/></svg>
          <span>Carl@funbrixo-demo.com</span>
        </li>
        <li>
          <svg viewBox="0 0 24 24" aria-hidden="true"><circle cx="12" cy="12" r="10"/><path d="M2 12h20M12 2c3 3 3 17 0 20M12 2c-3 3-3 17 0 20" stroke="#1b1b1d" stroke-width="1.6" fill="none"/></svg>
          <span>www.funbrixo-demo.com</span>
        </li>
      </ul>
    </div>
  </section>

  <section class="card card--front" aria-label="Card front">
    <div class="brand">
      <span class="brand__name">FunBrixo</span>
      <span class="brand__dot"></span>
    </div>
  </section>

</main>
</body>
</html>
```